Entrepreneur Podcast Cover Graphic Design

My wife and I just launched our podcast but we don't like the current cover. We want a new cover designed so it stands out and reflects the professionalism of our podcast. Attached is our current podcast cover design. We'd like to have it read "Rob & Kolette Interview Entrepreneurs on HARD CHOICES" - We'd also like to feature somehow that we have daily tips included.

Target Market(s)

entrepreneurs,business owners,start ups

Industry/Entity Type

Entrepreneur

Font styles to use
Sans Serif

Colors
0355a3
f37122
9bcb3c
fbed22
ec1f27

Requirements
Must have
• Our names listed: Rob & Kolette
Nice to have
• dark, bold colored background with an outline around the edge
Should not have
• no cartoons, no profanity

```html
<!DOCTYPE html>
<html lang="en">
<head>
<meta charset="UTF-8">
<title>Rob &amp; Kolette Interview Entrepreneurs on Hard Choices</title>
<link rel="stylesheet" href="https://fonts.googleapis.com/css2?family=Roboto:wght@300;700&display=swap">
<style>
  :root {
    --orange: #f37122;
    --red: #ec1f27;
    --paper: #ececec;
    --rule: #cccccc;
  }
  html, body {
    margin: 0;
    padding: 0;
    overflow: hidden;
    background: var(--paper);
  }
  .cover {
    position: relative;
    width: 1200px;
    height: 1200px;
    box-sizing: border-box;
    border: 11px solid var(--orange);
    background: var(--paper);
    overflow: hidden;
  }
  .artwork {
    position: absolute;
    top: -11px;
    left: -11px;
    width: 1200px;
    height: 1200px;
    font-family: "Roboto", Arial, sans-serif;
  }
  .hosts {
    font-weight: 700;
    font-size: 158px;
    fill: var(--orange);
  }
  .tagline,
  .tips-label {
    font-weight: 300;
    font-size: 84px;
    fill: var(--orange);
  }
  .title {
    font-weight: 700;
    fill: var(--red);
  }
  .title-main { font-size: 302px; }
  .title-sub { font-size: 194px; }
  .rule { fill: var(--rule); }
  .tips-check { fill: var(--red); }
</style>
</head>
<body>
  <main class="cover">
    <svg class="artwork" viewBox="0 0 1200 1200" role="group" aria-label="Rob &amp; Kolette Interview Entrepreneurs on Hard Choices. Includes daily tips.">
      <text class="hosts" x="104" y="232" textLength="998" lengthAdjust="spacingAndGlyphs">Rob &amp; Kolette</text>
      <text class="tagline" x="108" y="332" textLength="984" lengthAdjust="spacingAndGlyphs">Interview Entrepreneurs on</text>
      <text class="title title-main" x="95" y="606" textLength="996" lengthAdjust="spacing">HARD</text>
      <text class="title title-sub" x="114" y="796" textLength="977" lengthAdjust="spacing">CHOICES</text>
      <rect class="rule" x="116" y="927" width="968" height="3"/>
      <path class="tips-check" d="M212 988 L235 1005 L286 966 L288 969 L235 1024 Z"/>
      <text class="tips-label" x="320" y="1020" textLength="655" lengthAdjust="spacingAndGlyphs">Includes daily tips</text>
      <rect class="rule" x="116" y="1056" width="968" height="3"/>
    </svg>
  </main>
</body>
</html>
```